Initial website for sport tech startup

We are currently in the R&D phases of our new product. It’s a headband to prevent concussion in the soccer market initially.

We have 2 products, one that’s basic aimed at the youth market and the other more technology driven that’s aimed at the academies and professional market.

Initially the product will launch in the UK

Target Market(s)

Youth soccer players and parents in UK, Soccer Clubs, Federations.

Industry/Entity Type

Sporting Good

Coding

Coded - Design and coding required

Number of Pages Required

5+ page

Requirements
Must have
• Professional style that can be adapted and changed over the coming months.
Nice to have
• Ecommerce ability in the future.

```html
<!DOCTYPE html>
<html lang="en">
<head>
<meta charset="utf-8">
<title>Guardline — Head Protection for Sport</title>
<link rel="stylesheet" href="https://fonts.googleapis.com/css2?family=Barlow:wght@400;500;600&family=Roboto:wght@400;500&display=swap">
<style>
:root{
  --navy:#174a7e;
  --navy-dark:#0f3a66;
  --ink:#1d1d1d;
  --text:#555;
  --dark-band:#262222;
  --footer:#1f1f1f;
  --white:#fff;
  --card-bg:#f4f4f4;
}
*{box-sizing:border-box;margin:0;padding:0}
html,body{width:1200px;height:4432px;overflow:hidden}
body{font-family:"Roboto",sans-serif;color:var(--ink);background:var(--white);position:relative}
section,header,footer{position:relative;width:1200px}
.abs{position:absolute}
.heading{font-family:"Barlow",sans-serif;font-weight:500;color:var(--navy);text-transform:uppercase;letter-spacing:1px}
.btn{position:absolute;background:var(--navy);color:var(--white);font-family:"Barlow",sans-serif;font-weight:500;text-transform:uppercase;display:flex;align-items:center;justify-content:center;letter-spacing:.5px}
.photo{position:absolute}

/* header */
.site-header{height:132px}
.brand{left:90px;top:31px;width:315px;height:76px;border:4px solid var(--navy);display:flex;align-items:center;justify-content:center;font-family:"Barlow",sans-serif;font-weight:600;font-size:52px;color:#3a3a3a;letter-spacing:2px}
.phone{right:96px;top:22px;display:flex;align-items:center;gap:14px;font-family:"Barlow",sans-serif;font-size:22px;font-weight:500;color:#222}
.nav{right:90px;top:76px;display:flex;gap:20px;font-family:"Barlow",sans-serif;font-size:16px;font-weight:500;text-transform:uppercase;color:#222}
.nav .active{color:var(--navy);border-bottom:2px solid var(--navy)}

/* hero */
.hero{height:582px;background:linear-gradient(180deg,#3d4a38 0%,#52623f 45%,#3c4a2c 100%);overflow:hidden}
.hero .photo{inset:0}
.hero-copy{position:absolute;left:0;right:0;top:170px;text-align:center;color:var(--white)}
.hero-copy h1{font-family:"Barlow",sans-serif;font-weight:500;font-size:56px;letter-spacing:2px;line-height:1}
.hero-copy p{font-size:24px;line-height:36px;margin-top:14px}
.hero .btn{left:473px;top:329px;width:250px;height:76px;font-size:24px}

/* about */
.about{height:966px}
.about h2{left:90px;top:80px;font-size:40px}
.about h3{left:90px;top:143px;width:520px;font-size:19px;font-weight:500;line-height:31px;color:#222}
.about p{left:90px;top:220px;width:515px;font-size:15px;line-height:33px;color:var(--text)}
.about .btn{left:90px;top:443px;width:182px;height:57px;font-size:18px}
.about .photo{left:673px;top:84px;width:429px;height:410px;background:linear-gradient(160deg,#9fb4cc,#2d4d8c 55%,#c23a3a)}
.audience{position:absolute;top:542px;width:477px;height:301px;border-radius:6px;overflow:hidden;display:flex;align-items:center;justify-content:center}
.audience span{position:relative;font-family:"Barlow",sans-serif;font-weight:500;font-size:30px;color:var(--white);text-transform:uppercase;letter-spacing:1px}
.audience.players{left:91px;background:linear-gradient(180deg,#4e5748,#3b4a32)}
.audience.parents{left:625px;background:linear-gradient(180deg,#5c554d,#4a4038)}

/* opportunity */
.opportunity{height:507px;background:linear-gradient(180deg,#2b2626,#1f1c1c);color:var(--white);text-align:center}
.opportunity h2{position:absolute;left:0;right:0;top:38px;font-family:"Barlow",sans-serif;font-weight:500;font-size:40px;text-transform:uppercase;letter-spacing:1px}
.opportunity h3{position:absolute;left:0;right:0;top:97px;font-size:19px;font-weight:500}
.opportunity p{position:absolute;left:0;right:0;top:143px;font-size:15px;line-height:33px}
.stat{position:absolute;top:270px;width:220px;text-align:center}
.stat svg{display:block;margin:0 auto}
.stat .value{position:absolute;left:0;right:0;top:42px;font-family:"Barlow",sans-serif;font-size:38px}
.stat .label{font-family:"Barlow",sans-serif;font-weight:500;font-size:17px;line-height:27px;text-transform:uppercase;margin-top:14px}

/* products */
.products{height:520px}
.product-frame{left:90px;top:103px;width:428px;height:408px;border:1px solid #ccc;box-shadow:0 0 6px rgba(0,0,0,.15);background:radial-gradient(ellipse at 50% 50%,#5a5f66 0,#5a5f66 28%,#fff 30%)}
.products h2{left:597px;top:100px;font-size:40px}
.products h3{left:597px;top:162px;width:510px;font-size:19px;font-weight:500;line-height:32px;color:#222}
.products p{left:597px;top:238px;width:505px;font-size:15px;line-height:33.5px;color:var(--text);text-align:justify}
.products .btn{left:600px;top:450px;width:182px;height:58px;font-size:18px}

/* team */
.team{height:603px}
.team h2{left:0;right:0;top:98px;text-align:center;font-size:40px}
.member{position:absolute;top:177px;width:319px;height:325px;background:var(--card-bg);border:1px solid #ccc;box-shadow:0 2px 6px rgba(0,0,0,.2);text-align:center;padding:0 22px}
.member .avatar{width:112px;height:112px;border-radius:50%;margin:18px auto 0}
.member h4{font-family:"Barlow",sans-serif;font-weight:500;font-size:19px;margin-top:16px;text-transform:uppercase;color:#222}
.member .role{font-family:"Barlow",sans-serif;font-weight:500;font-size:15px;color:var(--navy);margin-top:4px}
.member p{font-size:14px;line-height:27px;color:#333;margin-top:6px}
.member .more{position:absolute;left:50%;bottom:18px;margin-left:-16px;width:32px;height:26px;background:var(--navy);color:var(--white);font-size:16px;line-height:26px}

/* reviews */
.reviews{height:319px;background:var(--navy-dark);color:var(--white);text-align:center}
.reviews h2{position:absolute;left:0;right:0;top:35px;font-family:"Barlow",sans-serif;font-weight:500;font-size:40px;text-transform:uppercase;letter-spacing:1px}
.reviews blockquote{position:absolute;left:290px;right:290px;top:113px;font-size:16px;line-height:32px}
.quote-mark{position:absolute;font-family:"Barlow",sans-serif;font-weight:600;font-size:72px;line-height:1}
.reviews cite{position:absolute;left:0;right:0;top:232px;font-style:normal;font-family:"Barlow",sans-serif;font-weight:500;font-size:20px;text-transform:uppercase}
.dots{position:absolute;left:0;right:0;display:flex;justify-content:center;gap:10px}
.dots i{width:10px;height:10px;border-radius:50%;background:var(--white);display:block}
.dots i.on{background:#222}

/* distribution */
.distribution{height:440px}
.distribution h2{left:0;right:0;top:98px;text-align:center;font-size:38px}
.distribution p{position:absolute;left:100px;right:100px;top:168px;text-align:center;font-size:16px;line-height:29px;color:var(--text)}
.partner{position:absolute;top:237px;width:236px;height:121px;background:var(--white);box-shadow:1px 2px 6px rgba(0,0,0,.25);display:flex;align-items:center;justify-content:center}
.partner div{width:110px;height:56px;border-radius:8px;background:#d4d8de}
.distribution .dots{top:406px}
.distribution .dots i{background:var(--white);border:2px solid var(--navy)}
.distribution .dots i.on{background:var(--navy)}

/* footer */
.site-footer{height:364px;background:var(--footer);color:var(--white)}
.foot-col{position:absolute;top:62px}
.foot-col h5{font-family:"Barlow",sans-serif;font-weight:500;font-size:20px;text-transform:uppercase;margin-bottom:14px}
.foot-col li{list-style:none;font-size:15px;line-height:32px;color:#ddd}
.foot-col p{font-size:15px;line-height:27px;color:#ddd;width:340px}
.subscribe{display:flex;margin-top:18px;width:335px;height:47px;border:2px solid var(--white)}
.subscribe span{flex:1;background:var(--white);color:#222;font-size:15px;line-height:43px;padding-left:8px}
.subscribe b{width:128px;background:var(--navy);font-family:"Barlow",sans-serif;font-weight:500;font-size:18px;line-height:43px;text-align:center}
.copyright{position:absolute;left:90px;top:327px;font-size:15px;font-weight:500}
.social{position:absolute;right:96px;top:328px;display:flex;gap:11px}
.social i{width:20px;height:20px;background:var(--white);border-radius:3px;display:block}
</style>
</head>
<body>

<header class="site-header">
  <div class="abs brand">GUARDLINE</div>
  <div class="abs phone">
    <svg width="30" height="30" viewBox="0 0 30 30" aria-hidden="true"><circle cx="15" cy="15" r="13" fill="none" stroke="#174a7e" stroke-width="2.5"/><path d="M10 9c1-1 2 0 3 2s0 2-1 3c1 2 2 3 4 4 1-1 1-2 3-1s3 2 2 3c-1 2-3 2-5 1-3-2-5-4-7-7-1-2-1-4 1-5z" fill="#174a7e"/></svg>
    +44 208 5550142
  </div>
  <nav class="abs nav">
    <span class="active">Home</span><span>About Us</span><span>Our Product</span><span>Team</span><span>Business</span><span>Contact Us</span>
  </nav>
</header>

<section class="hero">
  <div class="photo" role="img" aria-label="Photo of a professional football match with players down on the pitch after a head clash"></div>
  <div class="hero-copy">
    <h1>GUARDLINE</h1>
    <p>Guardline is designing and developing head protection<br>products to reduce the likelihood of concussion when playing sports.</p>
  </div>
  <div class="btn">Get Started</div>
</section>

<section class="about">
  <h2 class="abs heading">About Us</h2>
  <h3 class="abs">Guardline – Bringing Safety To The Sports Concussion Debate</h3>
  <p class="abs">Guardline is designing and developing head protection products to reduce the likelihood of concussion when playing sports. Exploring and understanding medical insights, material science and composites research, current and former players experiences and governing bodies guidelines has allowed Guardline to develop the safety, style.</p>
  <div class="btn">Read More</div>
  <div class="photo" role="img" aria-label="Photo of women footballers contesting a header"></div>
  <div class="audience players" role="img" aria-label="Photo of youth soccer players on the pitch"><span>Youth Soccer Players</span></div>
  <div class="audience parents" role="img" aria-label="Photo of a parent and child with a football"><span>Youth Soccer Parents</span></div>
</section>

<section class="opportunity">
  <h2>Size Of The Opportunity</h2>
  <h3>From Professionals To Non-league And Schools, The Problem Needs To Be Addressed.</h3>
  <p>A day doesn't go by without a report of a game being held up for a concussion injury or a player being<br>stretchered off up and down the country on a weekend,from youth football to men's and women's Sunday league.<br>In youth and high school soccer athletes, a concussion is the second most common injury sustained during match play.</p>
  <div class="stat" style="left:222px">
    <svg width="134" height="134" viewBox="0 0 134 134" aria-hidden="true"><circle cx="67" cy="67" r="60" fill="none" stroke="#174a7e" stroke-width="9"/><circle cx="67" cy="67" r="60" fill="none" stroke="#fff" stroke-width="9" stroke-dasharray="151 377"/></svg>
    <div class="value">40%</div>
    <div class="label">Injury From Head To<br>Player Contact</div>
  </div>
  <div class="stat" style="left:508px">
    <svg width="134" height="134" viewBox="0 0 134 134" aria-hidden="true"><circle cx="67" cy="67" r="60" fill="none" stroke="#174a7e" stroke-width="9"/><circle cx="67" cy="67" r="60" fill="none" stroke="#fff" stroke-width="9" stroke-dasharray="38 377" transform="rotate(20 67 67)"/></svg>
    <div class="value">10%</div>
    <div class="label">Injury From Head<br>To Ground</div>
  </div>
  <div class="stat" style="left:768px">
    <svg width="134" height="134" viewBox="0 0 134 134" aria-hidden="true"><circle cx="67" cy="67" r="60" fill="none" stroke="#174a7e" stroke-width="9"/><circle cx="67" cy="67" r="60" fill="none" stroke="#fff" stroke-width="9" stroke-dasharray="45 377" transform="rotate(20 67 67)"/></svg>
    <div class="value">12%</div>
    <div class="label">Injury From Head<br>To Ball</div>
  </div>
</section>

<section class="products">
  <div class="abs product-frame" role="img" aria-label="Illustration of the protective headband product"></div>
  <h2 class="abs heading">Products</h2>
  <h3 class="abs">A Technology Breakthrough In The Sport That Will Protect As Well As Allow For New Data Collection And Analytics.</h3>
  <p class="abs">Our initial product will be simplistic in function and design to ensure we get to market in 2020. Further versions of the product will incorporate data tracking technologies to enhance analytical streams available to players and clubs.Starting with soccer,followed by other markets such as netball and field hockey, where the same issues exist today.</p>
  <div class="btn">Read More</div>
</section>

<section class="team">
  <h2 class="abs heading">Team</h2>
  <div class="member" style="left:90px">
    <div class="avatar" role="img" aria-label="Portrait photo of Martin Hale" style="background:linear-gradient(135deg,#c94040,#8a8a8a)"></div>
    <h4>Martin Hale</h4>
    <div class="role">FOUNDER / CEO</div>
    <p>Martin has a wealth of experience of growing start-ups and exiting businesses,from professional services .</p>
    <div class="more">+</div>
  </div>
  <div class="member" style="left:439px">
    <div class="avatar" role="img" aria-label="Portrait photo of Sandra Pryce" style="background:linear-gradient(135deg,#b9c2cc,#56606a)"></div>
    <h4>Sandra Pryce</h4>
    <div class="role">CO –FOUNDER / COO</div>
    <p>Sandra has been planning and delivering commercial, large scale transformation projects within people.</p>
    <div class="more">+</div>
  </div>
  <div class="member" style="left:787px">
    <div class="avatar" role="img" aria-label="Portrait photo of Owen Talbot" style="background:linear-gradient(135deg,#d8d8d8,#6f6a64)"></div>
    <h4>Owen Talbot</h4>
    <div class="role">CCO</div>
    <p>Owen started his career in retail banking,later experience in corporate and private banking.</p>
    <div class="more">+</div>
  </div>
</section>

<section class="reviews">
  <h2>Real Customer Reviews</h2>
  <span class="quote-mark" style="left:250px;top:98px">“</span>
  <blockquote>We are seeing more and more children come to matches with home-made head protection. In addition, we are having more concern from parents about heading the ball and getting asked more about our guidelines on heading and head injuries.</blockquote>
  <span class="quote-mark" style="left:897px;top:180px">”</span>
  <cite>-Chief Executive, County League, North Region</cite>
  <div class="dots" style="top:280px"><i class="on"></i><i></i><i class="on"></i></div>
</section>

<section class="distribution">
  <h2 class="abs heading">Distribution</h2>
  <p>From parents to clubs to federations our model is simple; parents of youth players, parents of amateur players, professional players<br>and clubs,academies and all with the support of federations and unions.</p>
  <div class="partner" style="left:90px"><div></div></div>
  <div class="partner" style="left:351px"><div></div></div>
  <div class="partner" style="left:613px"><div></div></div>
  <div class="partner" style="left:866px"><div></div></div>
  <div class="dots"><i></i><i class="on"></i><i></i></div>
</section>

<footer class="site-footer">
  <div class="foot-col" style="left:90px">
    <h5>Quicks Links</h5>
    <ul><li>Home</li><li>About Us</li><li>Our Product</li><li>Team</li><li>Business</li><li>Contact Us</li></ul>
  </div>
  <div class="foot-col" style="left:286px">
    <h5>Other Links</h5>
    <ul><li>Research</li><li>Business</li><li>Market</li><li>Raise Spend</li></ul>
  </div>
  <div class="foot-col" style="left:501px">
    <h5>Contact Us</h5>
    <ul><li>14 Harbour View Road</li><li>Millbrook, MA 02100</li><li>+44 208 5550142</li><li>info@guardline.co.uk</li></ul>
  </div>
  <div class="foot-col" style="left:764px">
    <h5>News Letter</h5>
    <p>Guardline To Develop The Safety, Style, Form And Function Requirements Of A Suitable Product To Bring To Market In Q4 2020.</p>
    <div class="subscribe"><span>Enter the Email</span><b>SEND</b></div>
  </div>
  <div class="copyright">© Copyright 2020 Guardline.All Rights Reserved</div>
  <div class="social" aria-hidden="true"><i></i><i></i><i></i><i></i></div>
</footer>

</body>
</html>
```